Bright Wave Labs

We need a professional letter head format for our company. Now we have a logo but need to desing a new logo also. I have uploaded our old logo. Use the color in the logo and design a new one.

Dear Designers , Need to mention "BWL" and please dont use our old LOGO. we need a new catchy one.

```html
<!DOCTYPE html>
<html lang="en">
<head>
<meta charset="utf-8">
<title>Bright Wave Labs — Letterhead</title>
<link rel="stylesheet" href="https://fonts.googleapis.com/css2?family=Arimo:wght@700&family=Source+Sans+3:wght@400;600;700&display=swap">
<style>
  :root {
    --backdrop: #e6e6e6;
    --paper: #ffffff;
    --navy: #0f2238;
    --green: #8cc63f;
    --body-text: #58595b;
    --rule: #1b1b1b;
    --signature-tone: #d9dbe0;
  }
  * { margin: 0; padding: 0; box-sizing: border-box; }
  html, body {
    width: 1200px; height: 1200px; overflow: hidden;
    background: var(--backdrop);
  }
  .letterhead {
    position: absolute; left: 196px; top: 30px;
    width: 808px; height: 1140px;
    background: var(--paper);
    font-family: "Source Sans 3", sans-serif;
    color: var(--body-text);
  }
  .brand {
    position: absolute; left: 77px; top: 44px;
    display: flex; flex-direction: column; align-items: flex-start; gap: 10px;
  }
  .brand-dot {
    width: 62px; height: 62px; border-radius: 50%;
    background: var(--green);
  }
  .brand-name {
    font-family: "Source Sans 3", sans-serif;
    font-weight: 700; font-size: 16px; letter-spacing: 0.3px;
    color: var(--navy);
  }
  .salutation {
    position: absolute; left: 68px; top: 210px;
    font-family: "Arimo", sans-serif; font-weight: 700;
    font-size: 17.5px; color: var(--navy);
  }
  .letter-body {
    position: absolute; left: 68px; top: 248px; width: 676px;
  }
  .letter-body p {
    font-size: 16.2px; line-height: 21.1px;
    text-align: justify; margin-bottom: 21px;
  }
  .signature {
    position: absolute; left: 66px; top: 742px;
    width: 124px; height: 44px;
    background: var(--signature-tone); border-radius: 4px;
  }
  .closing {
    position: absolute; left: 70px; top: 774px;
    font-weight: 600; font-size: 16px; color: var(--navy);
  }
  .footer-bar {
    position: absolute; left: 58px; top: 1080px;
    width: 14px; height: 60px; background: var(--navy);
  }
  .footer-contact {
    position: absolute; left: 81px; top: 1079px;
    font-size: 11px; line-height: 16px; color: #111;
  }
  .footer-contact b { font-weight: 700; }
  .footer-contact .email { font-size: 13px; }
  .footer-rule {
    position: absolute; left: 72px; top: 1120px;
    width: 540px; height: 1px; background: var(--rule);
  }
  .web-tab {
    position: absolute; left: 588px; top: 1111px;
    width: 172px; height: 20px;
    background: var(--navy); color: var(--green);
    clip-path: polygon(5% 0, 96% 0, 100% 50%, 96% 100%, 5% 100%, 0 50%);
    font-size: 13px; line-height: 20px; text-align: center; letter-spacing: 0.3px;
  }
</style>
</head>
<body>
  <main class="letterhead">
    <header class="brand">
      <div class="brand-dot"></div>
      <div class="brand-name">BRIGHT WAVE LABS</div>
    </header>

    <h1 class="salutation">Dear Mr. John,</h1>

    <section class="letter-body">
      <p>Lorem Ipsum is simply dummy text of the printing and typesetting industry. Lorem Ipsum has been the industry's standard dummy text ever since the 1500s, when an unknown printer took a galley of type and scrambled it to make a type specimen book. It has survived not only five centuries, but also the leap into electronic typesetting, remaining essentially unchanged.</p>
      <p>The standard chunk of Lorem Ipsum used since the 1500s is reproduced below for those interested. Sections 1.10.32 and 1.10.33 from "de Finibus Bonorum et Malorum" by Cicero are also reproduced in their exact original form, accompanied by English versions from the 1914 translation by H. Rackham</p>
      <p>Lorem Ipsum is simply dummy text of the printing and typesetting industry. Lorem Ipsum has been the industry's standard dummy text ever since the 1500s, when an unknown printer took a galley of type and scrambled it to make a type specimen book. It has survived not only five centuries, but also the leap into electronic typesetting, remaining essentially unchanged. It was popularised in the</p>
      <p>The standard chunk of Lorem Ipsum used since the 1500s is reproduced below for those interested. Sections 1.10.32 and 1.10.33 from "de Finibus Bonorum et Malorum" by Cicero are also reproduced in their exact original form, accompanied by English versions from the 1914 translation by H. Rackham</p>
    </section>

    <div class="signature" role="img" aria-label="Handwritten signature"></div>
    <p class="closing">Valued customers,</p>

    <footer>
      <div class="footer-bar"></div>
      <div class="footer-contact">
        <div>Po. box 201, Street Name, City Name, Zip Code - 00000</div>
        <div><b>Tel:</b> (123) 456 0125 &nbsp;|&nbsp; <b>Mail:</b> <span class="email">info@brightwavelabs.com</span></div>
      </div>
      <div class="footer-rule"></div>
      <div class="web-tab">www.brightwavelabs.com</div>
    </footer>
  </main>
</body>
</html>
```